Bridgeway Health of Nations

Please design a business card that is colorful but at the same time easy to read. We are based out on Miami Florida. We are a small start up healthcare company that has been in operation for 1 year. Our clients are Hospitals, Insurance companies, and Manage Care health companies. We are growing quickly and lead the niche we are in. Please make the card 2 sided on the front will be the typical info. Logo, Company Name, Persons Name, Title, Cell #, Office #, Fax#, email, website. No address. On the back we will list 5 services that we do. For example Care Transitions, Case management, Risk assessment, Utilization Review.
Target Market(s)
CEO's and COO's of hospitals and healthcare companies.
Industry/Entity Type
Healthcare

```html
<!DOCTYPE html>
<html lang="en">
<head>
<meta charset="utf-8">
<title>Bridgeway Health of Nations – Business Card</title>
<link rel="stylesheet" href="https://fonts.googleapis.com/css2?family=Open+Sans:wght@300;400;600;700&display=swap">
<style>
  :root {
    --page: #e9e9e7;
    --card: #f4f4f4;
    --navy: #27308c;
    --blue-deep: #2a3a9a;
    --blue-bright: #1185c8;
    --stripe-blue: #0e4d9c;
    --stripe-green: #1a9a3a;
    --stripe-yellow: #e8d31d;
    --stripe-red: #d9232e;
    --text-blue: #2b3f9a;
    --white: #ffffff;
  }
  * { box-sizing: border-box; margin: 0; padding: 0; }
  html, body {
    width: 1200px; height: 900px; overflow: hidden;
    background: var(--page);
    font-family: "Open Sans", Arial, sans-serif;
  }
  .sheet {
    width: 1200px; height: 900px;
    display: flex; flex-direction: column; align-items: center; justify-content: center;
    gap: 56px;
  }
  .card {
    position: relative;
    width: 640px; height: 366px;
    background: var(--card);
    overflow: hidden;
    box-shadow: 0 2px 8px rgba(0,0,0,.12);
  }

  /* Back side */
  .card-back .brand {
    position: absolute; top: 78px; left: 150px;
    display: flex; align-items: center; gap: 14px;
  }
  .brand-dot {
    width: 34px; height: 34px; border-radius: 50%;
    background: var(--navy);
  }
  .brand-name {
    font-weight: 700; font-size: 26px; line-height: 1.1;
    color: var(--navy);
  }
  .services {
    position: absolute; right: 70px; top: 200px;
    list-style: none; text-align: right;
    color: var(--text-blue); font-size: 19px; line-height: 1.55;
  }
  .services li span::before { content: "• "; }
  .services li span + span { margin-left: 14px; }
  .color-band {
    position: absolute; left: 0; right: 0; bottom: 0; height: 24px;
    display: flex;
  }
  .color-band i { flex: 1; }
  .color-band .b { background: var(--stripe-blue); }
  .color-band .g { background: var(--stripe-green); }
  .color-band .y { background: var(--stripe-yellow); }
  .color-band .r { background: var(--stripe-red); }

  /* Front side */
  .card-front .brand {
    position: absolute; top: 38px; left: 170px;
    display: flex; align-items: center; gap: 14px;
  }
  .card-front .brand-name { font-size: 24px; }
  .contact-panel {
    position: absolute; left: 0; right: 0; bottom: 0; height: 212px;
    background: linear-gradient(160deg, var(--blue-deep) 0%, var(--blue-bright) 100%);
    color: var(--white);
    padding: 30px 48px 0 60px;
  }
  .person { display: flex; align-items: baseline; gap: 14px; }
  .person-name { font-weight: 300; font-size: 32px; letter-spacing: .5px; }
  .person-title { font-size: 15px; }
  .contact-lines { margin-top: 12px; font-size: 16px; line-height: 1.55; }
  .contact-lines .label { font-weight: 600; margin-right: 4px; }
  .contact-lines .item + .item { margin-left: 14px; }
  .label-t { color: var(--stripe-green); }
  .label-m { color: var(--stripe-yellow); }
  .label-f { color: var(--stripe-red); }
  .label-e { color: var(--stripe-green); }
  .website {
    position: absolute; right: 48px; bottom: 28px;
    font-weight: 700; font-size: 17px;
  }
</style>
</head>
<body>
<main class="sheet">

  <section class="card card-back" aria-label="Business card, back side">
    <div class="brand">
      <span class="brand-dot"></span>
      <span class="brand-name">Bridgeway Health<br>of Nations</span>
    </div>
    <ul class="services">
      <li><span>Care Transitions</span><span>Case management</span></li>
      <li><span>Risk assessment</span><span>Utilization Review</span></li>
    </ul>
    <div class="color-band"><i class="b"></i><i class="g"></i><i class="y"></i><i class="r"></i></div>
  </section>

  <section class="card card-front" aria-label="Business card, front side">
    <div class="brand">
      <span class="brand-dot"></span>
      <span class="brand-name">Bridgeway Health<br>of Nations</span>
    </div>
    <div class="contact-panel">
      <div class="person">
        <span class="person-name">MARCUS DELGADO</span>
        <span class="person-title">Operation Manager</span>
      </div>
      <div class="contact-lines">
        <div>
          <span class="item"><span class="label label-t">T</span>(305) 41 552 07 18</span>
          <span class="item"><span class="label label-m">M</span>(305) 62 774 19 30</span>
        </div>
        <div>
          <span class="item"><span class="label label-f">F</span>(305) 41 552 07 40</span>
          <span class="item"><span class="label label-e">E</span>marcus@bridgewayhealth.com</span>
        </div>
      </div>
      <div class="website">www.bridgewayhealth.com</div>
    </div>
  </section>

</main>
</body>
</html>
```